Dynamic Business Card for Sports Supplements Company

Hi! I'm looking for an awesome business card to match my existing sports supplement company. I have uploaded my current company logo and screenshot of the front page of my website.

I would like to have something dynamic and interesting and utilize the colors in the website - the reds and purples

The business card should be double sided and focus on a unique eye-catching design on the back and include all the relevant company info.

Most importantly, it should say somewhere: "Sign up on our website for a coupon code."

Target Market(s)

Mostly for women gym goers but it shouldn't be too feminine. It should be in keeping with the website design. It should flow and clearly be connected to it

Industry/Entity Type

Business

Contact Information for Business Card

Lorraine K. Vestal
CEO
LVestal@Quorvanexco.com
www.quorvanexco.com
555.417.3820
P.O. Box 47315
Harlow Ridge, Ohio 00000

Sign up on our website for a coupon code

Font styles to use
Serif
Sans Serif
Other font styles liked:
• Novecento font family and "Quorvanex" is in AR Destine font

Requirements
Must have
• One side should be a bold Quorvanex logo design. Even just the symbol itself may be o.k. (see attached file)

```html
<!DOCTYPE html>
<html lang="en">
<head>
<meta charset="utf-8">
<title>Quorvanex Business Card</title>
<link rel="stylesheet" href="https://fonts.googleapis.com/css2?family=Open+Sans:ital,wght@0,400;0,600;0,700;1,400&display=swap">
<style>
  :root {
    --ink: #000000;
    --brand-red: #ec1c24;
    --paper: #ffffff;
    --backdrop: #e6e4e1;
    --card-w: 615px;
    --card-h: 352px;
  }
  * { margin: 0; padding: 0; box-sizing: border-box; }
  html, body {
    width: 1200px;
    height: 987px;
    overflow: hidden;
    background: var(--backdrop);
    font-family: "Open Sans", sans-serif;
  }
  .canvas { position: relative; width: 1200px; height: 987px; }
  .card {
    position: absolute;
    width: var(--card-w);
    height: var(--card-h);
    background: var(--ink);
    overflow: hidden;
    color: var(--paper);
  }
  .card--front { left: 293px; top: 130px; }
  .card--back  { left: 292px; top: 506px; }

  .card__shapes { position: absolute; inset: 0; width: 100%; height: 100%; }

  .brand {
    position: absolute;
    left: 44px;
    top: 128px;
    display: flex;
    align-items: center;
    gap: 10px;
  }
  .brand__mark { width: 16px; height: 16px; background: var(--brand-red); }
  .brand__name {
    font-weight: 700;
    font-size: 28px;
    letter-spacing: 1px;
    text-transform: uppercase;
    color: var(--paper);
    line-height: 1;
  }

  .contact {
    position: absolute;
    right: 22px;
    top: 178px;
    text-align: right;
  }
  .contact__name { font-size: 22px; font-weight: 600; line-height: 30px; }
  .contact__role { font-size: 16px; line-height: 24px; margin-bottom: 4px; }
  .contact__list { list-style: none; }
  .contact__item {
    display: flex;
    justify-content: flex-end;
    align-items: center;
    gap: 6px;
    font-size: 15px;
    line-height: 24px;
  }
  .contact__icon { width: 14px; height: 14px; flex: none; }

  .back-brand {
    position: absolute;
    left: 0; right: 0;
    top: 118px;
    display: flex;
    justify-content: center;
    align-items: center;
    gap: 16px;
  }
  .back-brand__mark { width: 30px; height: 30px; background: var(--brand-red); }
  .back-brand__name {
    font-weight: 700;
    font-size: 54px;
    letter-spacing: 2px;
    text-transform: uppercase;
    color: var(--paper);
    line-height: 1;
  }
  .promo {
    position: absolute;
    left: 0; right: 0;
    top: 288px;
    text-align: center;
    font-style: italic;
    font-size: 16px;
  }
</style>
</head>
<body>
<main class="canvas">

  <section class="card card--front" aria-label="Business card front">
    <svg class="card__shapes" viewBox="0 0 615 352" aria-hidden="true">
      <polygon points="615,0 615,352 154,352" fill="var(--brand-red)"/>
      <polygon points="0,235 0,352 154,352" fill="var(--paper)"/>
    </svg>

    <div class="brand">
      <span class="brand__mark"></span>
      <span class="brand__name">Quorvanex</span>
    </div>

    <div class="contact">
      <p class="contact__name">Lorraine K. Vestal</p>
      <p class="contact__role">CEO</p>
      <ul class="contact__list">
        <li class="contact__item">555.417.3820
          <svg class="contact__icon" viewBox="0 0 16 16" aria-hidden="true"><path fill="#fff" d="M3.6 1.2l2.3 2.6-1.3 1.7c.9 2 2.6 3.8 4.7 4.8l1.7-1.4 2.7 2.3-1.3 2.5C7 13.5 2.4 8.8 1.1 2.6z"/></svg>
        </li>
        <li class="contact__item">LVestal@Quorvanexco.com
          <svg class="contact__icon" viewBox="0 0 16 16" aria-hidden="true"><rect x="1" y="3" width="14" height="10" fill="#fff"/><path d="M1.5 3.5L8 9l6.5-5.5" stroke="var(--brand-red)" stroke-width="1.3" fill="none"/></svg>
        </li>
        <li class="contact__item">www.quorvanexco.com
          <svg class="contact__icon" viewBox="0 0 16 16" aria-hidden="true"><circle cx="8" cy="8" r="7" fill="#fff"/><path d="M5 4c2 1 1 3 3 3s1 3 0 4M10 3c-1 2 1 2 2 3" stroke="var(--brand-red)" stroke-width="1.4" fill="none"/></svg>
        </li>
        <li class="contact__item">P.O. Box 47315, Harlow Ridge, Ohio 00000</li>
      </ul>
    </div>
  </section>

  <section class="card card--back" aria-label="Business card back">
    <div class="back-brand">
      <span class="back-brand__mark"></span>
      <span class="back-brand__name">Quorvanex</span>
    </div>
    <p class="promo">Sign up on our website for a coupon code</p>
  </section>

</main>
</body>
</html>
```